Personal Injury Law Firm needs folder design

Need a folder design for our personal injury law firm, Corrow & Talmidge, LLC. to give to all of our clients with their documents at the end of their case. I've attached our branding guide. We are branded as the 5 star law firm that fights for our clients like family. It should incorporate our colors or Green and White. We'd like to convey a message of moving on to the next chapter after finishing their case.

```html
<!DOCTYPE html>
<html lang="en">
<head>
<meta charset="utf-8">
<title>Corrow &amp; Talmidge, LLC. – Client Folder</title>
<link rel="stylesheet" href="https://fonts.googleapis.com/css2?family=Cinzel:wght@400;700&family=Poppins:wght@400;500;600;700&display=swap">
<style>
  :root {
    --green: #05a37a;
    --green-dark: #0a8a66;
    --ink: #222222;
    --white: #ffffff;
    --gold: #f5d000;
    --stage: #cfcfcf;
    --rule: #3a4a44;
  }
  * { box-sizing: border-box; margin: 0; padding: 0; }
  html, body { width: 866px; height: 1200px; overflow: hidden; }
  body { background: var(--stage); position: relative; font-family: "Poppins", sans-serif; }

  .folder {
    position: absolute; left: 20px; top: 308px;
    width: 826px; height: 584px;
    background: var(--white);
    overflow: hidden;
    box-shadow: 0 10px 24px rgba(0,0,0,.25);
  }

  /* back panel */
  .back-backdrop {
    position: absolute; left: 0; top: 0; width: 420px; height: 584px;
    background: radial-gradient(ellipse at 35% 20%, #e6e6e6 0%, #f3f3f3 45%, rgba(255,255,255,0) 75%),
                linear-gradient(180deg, #eeeeee 0%, #f7f7f7 55%, #ffffff 100%);
  }
  .tagline { position: absolute; left: 0; width: 390px; text-align: center; color: var(--ink); }
  .stars { position: absolute; left: 125px; top: 141px; }
  .tagline-small { top: 168px; font-size: 25px; font-weight: 500; letter-spacing: 3px; }
  .tagline-big { top: 192px; font-size: 40px; font-weight: 700; letter-spacing: -.5px; line-height: 1.1; }

  .brand { position: absolute; display: flex; align-items: center; gap: 7px; }
  .brand-mark { background: var(--green); display: block; }
  .brand-name { font-family: "Cinzel", serif; font-weight: 400; color: var(--green); white-space: nowrap; }
  .brand--back { left: 93px; top: 265px; }
  .brand--back .brand-mark { width: 48px; height: 40px; }
  .brand--back .brand-name { font-size: 13.5px; }
  .brand--front { left: 446px; top: 40px; }
  .brand--front .brand-mark { width: 59px; height: 48px; }
  .brand--front .brand-name { font-size: 16px; }

  .contact { position: absolute; left: 0; width: 390px; text-align: center; font-size: 12.5px; color: var(--ink); line-height: 16px; }
  .contact-icon { position: absolute; left: 155px; width: 88px; height: 18px; }

  /* front panel */
  .accent-band { position: absolute; left: 728px; width: 98px; background: var(--green); }
  .accent-band--top { top: 0; height: 137px; }
  .accent-band--bottom { top: 383px; height: 201px; }
  .hero-photo {
    position: absolute; left: 445px; top: 140px; width: 381px; height: 241px;
    background: linear-gradient(160deg, #8e8a84 0%, #bdb8ae 35%, #6f6a63 70%, #3a3633 100%);
  }
  .hero-frame { position: absolute; left: 475px; top: 165px; width: 360px; height: 239px; border: 1px solid var(--gold); }
  .headline { position: absolute; left: 446px; top: 434px; font-family: "Cinzel", serif; line-height: 24px; }
  .headline-lead { font-size: 23px; color: var(--ink); font-weight: 400; }
  .headline-main { font-size: 24px; color: var(--green); font-weight: 700; }
  .front-web { position: absolute; left: 446px; top: 533px; font-size: 13px; letter-spacing: 2.4px; color: var(--ink); }
  .front-web strong { color: var(--green); font-weight: 600; }
</style>
</head>
<body>
  <main class="folder">
    <section class="back-panel">
      <div class="back-backdrop" role="img" aria-label="Faint grey photo of a roadside accident scene with a Lady Justice statue"></div>

      <svg class="stars" width="140" height="24" viewBox="0 0 140 24" aria-label="Five stars">
        <defs><polygon id="star" points="12,1 15,9 23,9 16.5,14 19,22 12,17 5,22 7.5,14 1,9 9,9" fill="#f5d000"/></defs>
        <use href="#star" x="0"/><use href="#star" x="23"/><use href="#star" x="46" y="-1"/><use href="#star" x="69"/><use href="#star" x="92"/>
      </svg>
      <p class="tagline tagline-small">THE 5 STAR</p>
      <p class="tagline tagline-big">LAW FIRM</p>

      <div class="brand brand--back"><span class="brand-mark"></span><span class="brand-name">Corrow &amp; Talmidge, LLC.</span></div>

      <svg class="contact-icon" style="top:341px" viewBox="0 0 88 18"><path d="M0 9h34M54 9h34" stroke="#3a4a44" stroke-width="1.2"/><circle cx="44" cy="9" r="9" fill="#05a37a"/><path d="M44 4a3.5 3.5 0 0 1 3.5 3.5c0 2.5-3.5 6-3.5 6s-3.5-3.5-3.5-6A3.5 3.5 0 0 1 44 4z" fill="#fff"/><circle cx="44" cy="7.5" r="1.3" fill="#05a37a"/></svg>
      <p class="contact" style="top:363px">4120 Harborview Court<br>Palm Cove, FL 33900</p>

      <svg class="contact-icon" style="top:404px" viewBox="0 0 88 18"><path d="M0 9h34M54 9h34" stroke="#3a4a44" stroke-width="1.2"/><circle cx="44" cy="9" r="9" fill="#05a37a"/><path d="M40.5 5c1-1 1.8 0 2.4 1s.3 1.5-.3 2c.5 1.3 1.4 2.2 2.6 2.7.5-.6 1-.9 2-.3s2 1.3 1 2.3c-1.6 1.6-4.5.5-6.4-1.5s-2.9-4.6-1.3-6.2z" fill="#fff"/></svg>
      <p class="contact" style="top:430px">(555) 014-2290</p>

      <svg class="contact-icon" style="top:458px" viewBox="0 0 88 18"><path d="M0 9h34M54 9h34" stroke="#3a4a44" stroke-width="1.2"/><circle cx="44" cy="9" r="9" fill="#05a37a"/><rect x="39.5" y="5.5" width="9" height="7" fill="#fff"/><path d="M39.5 5.5l4.5 4 4.5-4" stroke="#05a37a" stroke-width="1" fill="none"/></svg>
      <p class="contact" style="top:482px">info@corrowtalmidge.com</p>

      <svg class="contact-icon" style="top:512px" viewBox="0 0 88 18"><path d="M0 9h34M54 9h34" stroke="#3a4a44" stroke-width="1.2"/><circle cx="44" cy="9" r="9" fill="#05a37a"/><g stroke="#fff" stroke-width="1" fill="none"><circle cx="44" cy="9" r="4.5"/><ellipse cx="44" cy="9" rx="2" ry="4.5"/><path d="M39.5 9h9"/></g></svg>
      <p class="contact" style="top:533px">www.corrowtalmidge.com</p>
    </section>

    <section class="front-panel">
      <div class="brand brand--front"><span class="brand-mark"></span><span class="brand-name">Corrow &amp; Talmidge, LLC.</span></div>
      <div class="accent-band accent-band--top"></div>
      <div class="hero-photo" role="img" aria-label="Photo of the legal team standing before the stone columns of a courthouse"></div>
      <div class="hero-frame"></div>
      <div class="accent-band accent-band--bottom"></div>
      <h1 class="headline">
        <span class="headline-lead">YOUR FLORIDA</span><br>
        <span class="headline-main">PERSONAL INJURY<br>ATTORNEYS</span>
      </h1>
      <p class="front-web">www.<strong>corrowtalmidge</strong>.com</p>
    </section>
  </main>
</body>
</html>
```